Keystone ridge construction brochure

i would like a brochure that can be send to clients digitally and printed. we are a geotechnical, foundation, and concrete company. I attached info below

Target Market(s)

Construction managers, general contractors, developers, municipalities, private, and commercial partners.

Industry/Entity Type

Geotechnical / foundation

Font styles to use
Serif
Other font styles liked:
• Maybe same as logo

Colors
0054AA
0677BA
7BADD7
CADEEF
E8F1F8

```html
<!DOCTYPE html>
<html lang="en">
<head>
<meta charset="utf-8">
<title>Keystone Ridge Construction Brochure</title>
<link href="https://fonts.googleapis.com/css2?family=Roboto:wght@400;500;700;900&family=Manrope:wght@400;500;600;700&display=swap" rel="stylesheet">
<style>
  :root {
    --stage: #4a4a4a;
    --paper: #ffffff;
    --navy: #0c1d42;
    --slate: #555557;
    --ink: #2b2b2b;
    --muted: #555555;
    --rule: #0c1d42;
  }
  * { margin: 0; padding: 0; box-sizing: border-box; }
  html, body { width: 1200px; height: 2844px; overflow: hidden; }
  body { background: var(--stage); font-family: "Manrope", sans-serif; color: var(--ink); position: relative; }

  .page { position: absolute; left: 135px; width: 931px; height: 1206px; background: var(--paper); overflow: hidden; box-shadow: 0 6px 24px rgba(0,0,0,.35); }
  .page--front { top: 150px; }
  .page--back { top: 1488px; }

  /* front */
  .brand { position: absolute; top: 56px; left: 0; width: 100%; text-align: center; font-family: "Roboto", sans-serif; font-weight: 700; font-size: 33px; letter-spacing: 1px; color: var(--navy); }
  .headline { position: absolute; top: 124px; width: 100%; text-align: center; font-family: "Roboto", sans-serif; color: var(--navy); }
  .headline__top { display: block; font-size: 56px; font-weight: 500; color: var(--slate); line-height: 60px; }
  .headline__bottom { display: block; font-size: 62px; font-weight: 900; line-height: 62px; }
  .service-band { position: absolute; top: 264px; left: 0; width: 100%; height: 73px; background: var(--slate); color: #fff; font-family: "Roboto", sans-serif; font-size: 31px; letter-spacing: 2.5px; text-align: center; line-height: 73px; }
  .intro { position: absolute; top: 362px; left: 90px; width: 751px; text-align: center; font-size: 17px; line-height: 27px; color: var(--ink); }
  .pillars { position: absolute; top: 469px; left: 0; width: 100%; }
  .pillar { position: absolute; width: 210px; text-align: center; }
  .pillar__icon { width: 78px; height: 78px; margin: 0 auto; display: block; }
  .pillar__title { margin-top: 14px; font-size: 16px; font-weight: 700; color: var(--navy); }
  .pillar__text { margin-top: 6px; font-size: 14px; line-height: 22px; color: var(--muted); }
  .hero-photo { position: absolute; left: 0; top: 690px; width: 100%; height: 516px; background: linear-gradient(180deg, #aab6c4 0%, #c9cfd6 30%, #9ea3a7 55%, #4f6e3a 68%, #3c3f41 100%); }

  /* back */
  .cover-photo { position: absolute; top: 0; left: 0; width: 100%; height: 543px; background: radial-gradient(ellipse at 60% 45%, #e3e6e9 0%, #9aa3ab 35%, #4a525a 75%, #2e353c 100%); }
  .title-box { position: absolute; left: 64px; top: 355px; width: 428px; height: 241px; background: var(--navy); }
  .title-box::after { content: ""; position: absolute; inset: 18px; border: 1px solid rgba(255,255,255,.35); }
  .title-box__main { position: absolute; left: 41px; top: 42px; font-family: "Roboto", sans-serif; font-weight: 900; font-size: 58px; color: #fff; line-height: 62px; }
  .title-box__sub { position: absolute; left: 44px; top: 112px; font-family: "Roboto", sans-serif; font-weight: 700; font-size: 35px; color: #fff; line-height: 42px; }
  .about { position: absolute; left: 64px; top: 628px; width: 376px; font-size: 15.5px; line-height: 28px; text-align: justify; color: var(--ink); }
  .about p + p { margin-top: 28px; }
  .section-tab { position: absolute; height: 48px; background: var(--slate); color: #fff; font-family: "Roboto", sans-serif; font-weight: 500; font-size: 20.5px; line-height: 48px; }
  .section-tab--right { left: 530px; width: 401px; padding-left: 40px; clip-path: polygon(20px 0, 100% 0, 100% 100%, 0 100%); }
  .section-tab--left { left: 0; width: 363px; padding-left: 63px; clip-path: polygon(0 0, 343px 0, 100% 100%, 0 100%); }
  .checklist { position: absolute; list-style: none; font-size: 16.5px; color: var(--ink); }
  .checklist li { height: 31.5px; display: flex; align-items: center; }
  .checklist svg { width: 16px; height: 16px; margin-right: 14px; flex: none; }
  .contact-bar { position: absolute; left: 492px; top: 1116px; width: 439px; height: 78px; background: var(--slate); color: #fff; }
  .contact-bar__icon { position: absolute; left: 464px; top: 1128px; width: 54px; height: 62px; background: var(--navy); display: flex; align-items: center; justify-content: center; }
  .contact-bar__phone { position: absolute; left: 33px; top: 6px; font-family: "Roboto", sans-serif; font-weight: 700; font-size: 36px; line-height: 44px; }
  .contact-bar__links { position: absolute; left: 33px; top: 51px; font-size: 12px; white-space: nowrap; }
  .contact-bar__links span { margin: 0 10px; }
  .page-rule { position: absolute; left: 0; bottom: 4px; width: 100%; height: 2px; background: var(--rule); }
</style>
</head>
<body>

<svg width="0" height="0" style="position:absolute">
  <defs>
    <symbol id="tick" viewBox="0 0 16 16">
      <circle cx="8" cy="8" r="8" fill="#2b2b2b"/>
      <path d="M4.3 8.3 L7 10.8 L11.8 5.4" fill="none" stroke="#fff" stroke-width="2" stroke-linecap="round" stroke-linejoin="round"/>
    </symbol>
  </defs>
</svg>

<section class="page page--front">
  <div class="brand">KEYSTONE RIDGE</div>
  <h1 class="headline">
    <span class="headline__top">BUILT ON STRENGTH.</span>
    <span class="headline__bottom">FOCUSED ON SOLUTIONS.</span>
  </h1>
  <div class="service-band">GEOTECHNICAL. FOUNDATION. CONCRETE.</div>
  <p class="intro">Strong foundations begin with trusted expertise. Keystone Ridge Construction delivers reliable geotechnical, foundation, and concrete solutions built for performance, safety, and long-term success.</p>

  <div class="pillars">
    <div class="pillar" style="left:114px">
      <svg class="pillar__icon" viewBox="0 0 78 78"><circle cx="39" cy="39" r="39" fill="#0c1d42"/><g fill="none" stroke="#fff" stroke-width="1.8" stroke-linejoin="round"><path d="M24 40 a15 15 0 0 1 30 0 Z"/><path d="M20 40 h38"/><circle cx="39" cy="51" r="6"/><path d="M39 25 v-4 M33 27 v6 M45 27 v6"/></g></svg>
      <div class="pillar__title">Engineering Excellence</div>
      <div class="pillar__text">Our experienced professionals deliver practical, innovative solutions tailored to every project.</div>
    </div>
    <div class="pillar" style="left:360px">
      <svg class="pillar__icon" viewBox="0 0 78 78"><circle cx="39" cy="39" r="39" fill="#0c1d42"/><g fill="none" stroke="#fff" stroke-width="1.8" stroke-linejoin="round"><rect x="38" y="28" width="18" height="26" rx="2"/><path d="M42 35 h10 M42 41 h10 M42 47 h10"/><path d="M23 40 l8 -3 l8 3 v6 c0 5 -4 8 -8 10 c-4 -2 -8 -5 -8 -10 Z"/><path d="M27 46 l3 3 l5 -5"/></g></svg>
      <div class="pillar__title">Safety First</div>
      <div class="pillar__text">Safety is integrated into every phase of our work, ensuring protection for our team, clients, and job sites.</div>
    </div>
    <div class="pillar" style="left:606px">
      <svg class="pillar__icon" viewBox="0 0 78 78"><circle cx="39" cy="39" r="39" fill="#0c1d42"/><g fill="none" stroke="#fff" stroke-width="1.8"><circle cx="39" cy="39" r="20" stroke-dasharray="4 2.5"/><circle cx="39" cy="39" r="13"/><path d="M33 39 l4 4 l8 -8" stroke-linecap="round" stroke-linejoin="round"/></g></svg>
      <div class="pillar__title">Quality You Can Trust</div>
      <div class="pillar__text">We use proven methods, premium materials, and strict quality control to exceed expectations.</div>
    </div>
  </div>

  <div class="hero-photo" role="img" aria-label="Photo of a large modern concrete warehouse and office building with parking lot and green lawn"></div>
</section>

<section class="page page--back">
  <div class="cover-photo" role="img" aria-label="Photo of a long concrete tunnel of repeating triangular arches with light and shadow"></div>
  <div class="title-box">
    <div class="title-box__main">LET'S BUILD</div>
    <div class="title-box__sub">SOMETHING THAT<br>LASTS</div>
  </div>

  <div class="about">
    <p>Keystone Ridge Construction specializes in geotechnical services, foundation systems, and concrete construction for projects of every scale.</p>
    <p>Our mission is simple—to provide dependable construction solutions that create safe, stable, and long-lasting structures. We believe every successful project starts with a solid foundation, and we're committed to delivering excellence from the ground up.</p>
  </div>

  <div class="section-tab section-tab--right" style="top:558px">FOUNDATION SOLUTIONS</div>
  <ul class="checklist" style="left:584px; top:624px">
    <li><svg><use href="#tick"/></svg>Deep Foundations</li>
    <li><svg><use href="#tick"/></svg>Drilled Shafts</li>
    <li><svg><use href="#tick"/></svg>Helical Piles</li>
    <li><svg><use href="#tick"/></svg>Micropiles</li>
    <li><svg><use href="#tick"/></svg>Retaining Structures</li>
    <li><svg><use href="#tick"/></svg>Shoring Systems</li>
  </ul>

  <div class="section-tab section-tab--right" style="top:843px">CONCRETE CONSTRUCTION</div>
  <ul class="checklist" style="left:584px; top:909px">
    <li><svg><use href="#tick"/></svg>Structural Concrete</li>
    <li><svg><use href="#tick"/></svg>Reinforced Foundations</li>
    <li><svg><use href="#tick"/></svg>Slabs &amp; Footings</li>
    <li><svg><use href="#tick"/></svg>Concrete Walls</li>
    <li><svg><use href="#tick"/></svg>Equipment Pads</li>
    <li><svg><use href="#tick"/></svg>Commercial &amp; Industrial Concrete</li>
  </ul>

  <div class="section-tab section-tab--left" style="top:940px">GEOTECHNICAL SERVICES</div>
  <ul class="checklist" style="left:100px; top:1006px">
    <li><svg><use href="#tick"/></svg>Site Investigation</li>
    <li><svg><use href="#tick"/></svg>Soil Testing &amp; Analysis</li>
    <li><svg><use href="#tick"/></svg>Ground Improvement</li>
    <li><svg><use href="#tick"/></svg>Engineering Recommendations</li>
    <li><svg><use href="#tick"/></svg>Earth Retention Solutions</li>
  </ul>

  <div class="contact-bar">
    <div class="contact-bar__phone">+1 555 010 (0199)</div>
    <div class="contact-bar__links">info@keystoneridgebuild.com<span>|</span>www.keystoneridgebuild.com</div>
  </div>
  <div class="contact-bar__icon">
    <svg width="34" height="34" viewBox="0 0 34 34" fill="none" stroke="#fff" stroke-width="1.6" stroke-linecap="round" stroke-linejoin="round"><path d="M5 18 a12 12 0 0 1 24 0"/><rect x="3" y="17" width="5" height="8" rx="2"/><rect x="26" y="17" width="5" height="8" rx="2"/><path d="M11 14 h12 a2 2 0 0 1 2 2 v7 a2 2 0 0 1 -2 2 h-6 l-4 3 v-3 h-2 a2 2 0 0 1 -2 -2 v-7 a2 2 0 0 1 2 -2 Z"/><path d="M14 19.5 h0.1 M17 19.5 h0.1 M20 19.5 h0.1"/></svg>
  </div>
  <div class="page-rule"></div>
</section>

</body>
</html>
```